The most modern business card ever !!!

Our company call “Vendalo”. Vendalo is a technology company specialized in cruises solutions. Out main product is a platform to reserve cruises. This is a revolutionary platform that make easier to travel agencies and final users to reserve cruises across dozen companies like tibba, wernu, hpv, dgb, etc..We are a “start up”, with a young team of developers and we want to transmit it.. For it, we want something different, a modern business card that represent cruises and technology.. When someone receive this card, this person should say: wowww this is different… this is modern… this is a cruise related company..
- diferent, modern
- traditions business card

```html
<!DOCTYPE html>
<html lang="en">
<head>
<meta charset="utf-8">
<title>Vendalo – Business Card</title>
<link rel="stylesheet" href="https://fonts.googleapis.com/css2?family=Open+Sans:wght@400;600&family=Crimson+Text:wght@400&display=swap">
<style>
  :root {
    --page-bg: #e9eaec;
    --card-top: #f4f5f6;
    --card-bottom: #e3e6e9;
    --card-edge: #c9ccd0;
    --ink: #1d1e20;
    --ink-soft: #2b2c2f;
    --accent: #1f7fa8;
    --accent-light: #3ea7e0;
    --accent-deep: #2a86b5;
  }
  * { margin: 0; padding: 0; box-sizing: border-box; }
  html, body {
    width: 1200px;
    height: 970px;
    overflow: hidden;
    background: var(--page-bg);
  }
  .canvas {
    position: relative;
    width: 1200px;
    height: 970px;
  }
  .business-card {
    position: absolute;
    left: 100px;
    top: 200px;
    width: 1000px;
    height: 570px;
    border-radius: 26px;
    border: 1.5px solid var(--card-edge);
    background: linear-gradient(160deg, var(--card-top), var(--card-bottom));
    box-shadow: 0 18px 40px rgba(0, 0, 0, 0.12);
    overflow: hidden;
  }
  .brand-mark-area {
    position: absolute;
    left: 0;
    top: 104px;
    width: 330px;
    height: 372px;
    background: linear-gradient(135deg, var(--accent-light), var(--accent-deep));
    opacity: 0.85;
  }
  .identity {
    position: absolute;
    left: 567px;
    top: 100px;
    font-family: "Open Sans", sans-serif;
  }
  .wordmark {
    font-size: 60px;
    font-weight: 600;
    color: var(--ink);
    letter-spacing: 1px;
    line-height: 1;
  }
  .person-name {
    margin-top: 62px;
    font-size: 33px;
    font-weight: 400;
    color: var(--ink-soft);
    line-height: 1;
  }
  .job-title {
    margin-top: 12px;
    font-family: "Crimson Text", serif;
    font-size: 22px;
    color: var(--accent);
    line-height: 1;
  }
  .divider {
    margin-top: 28px;
    width: 82px;
    height: 4px;
    background: var(--accent);
  }
  .contact-list {
    list-style: none;
    margin-top: 44px;
  }
  .contact-item {
    display: flex;
    align-items: center;
    gap: 16px;
    height: 42px;
    font-size: 22px;
    color: var(--ink);
  }
  .contact-icon {
    width: 20px;
    height: 20px;
    flex: none;
  }
</style>
</head>
<body>
<div class="canvas">
  <div class="business-card">
    <div class="brand-mark-area" role="img" aria-label="Brand mark area"></div>

    <div class="identity">
      <div class="wordmark">Vendalo</div>
      <div class="person-name">YOUR NAME</div>
      <div class="job-title">Job title</div>
      <div class="divider"></div>

      <ul class="contact-list">
        <li class="contact-item">
          <svg class="contact-icon" viewBox="0 0 20 20" aria-hidden="true">
            <path d="M2 7 Q10 1 18 7 L16 9 L13 7.5 L13 6 Q10 5 7 6 L7 7.5 L4 9 Z" fill="var(--accent)"/>
            <rect x="4" y="10" width="12" height="7" rx="1.5" fill="var(--accent)"/>
            <circle cx="10" cy="13.5" r="1.8" fill="var(--card-top)"/>
          </svg>
          <span>000 000 0000</span>
        </li>
        <li class="contact-item">
          <svg class="contact-icon" viewBox="0 0 20 20" aria-hidden="true">
            <rect x="1.5" y="4.5" width="17" height="11" fill="var(--accent)"/>
            <path d="M1.5 4.5 L10 11 L18.5 4.5" fill="none" stroke="var(--card-top)" stroke-width="1.4"/>
          </svg>
          <span>youremail@xyz.com</span>
        </li>
        <li class="contact-item">
          <svg class="contact-icon" viewBox="0 0 20 20" aria-hidden="true" fill="none" stroke="var(--accent)" stroke-width="1.4">
            <circle cx="10" cy="10" r="8"/>
            <ellipse cx="10" cy="10" rx="3.5" ry="8"/>
            <line x1="2" y1="10" x2="18" y2="10"/>
            <line x1="3.5" y1="6" x2="16.5" y2="6"/>
            <line x1="3.5" y1="14" x2="16.5" y2="14"/>
          </svg>
          <span>www.yourwebsite.com</span>
        </li>
      </ul>
    </div>
  </div>
</div>
</body>
</html>
```